Buch-/eBook-Cover für Traumatherapeutin
Zielgruppe
Ich bin Traumatherapeutin und schreibe ein Buch zum Thema Trauma bearbeiten.
Meine Zielgruppe sucht Heilung, Genesung, Selbstliebe etc.
Aufgabenstellung
Buchcover
Bitte erstell mir ein modernes positives inspirierendes Buchcover mit dem
Titel: 'Morgenlicht NEU entdecken“
Untertitel: „Spüre den Mut der ganz in dir wohnt“
Dr. Mira Kessow
Ich hätte gerne ein modernes Buch, das entweder einen Bezug zum Thema Trauma hat oder aber einfach stylische Schriftzüge. Bin aber auch offen für andere Vorschläge.
Dunkelblau, weiß und türkis oder auch rosa mag ich ganz gerne. Wobei Dunkelblau, weiß und türkis meine Favoriten sind und mit rosa höchstens kleinere Akzente gesetzt werden sollten.
Das Buchcover soll modern sein und direkt ansprechen. Gerne eine originelle Lösung, oder etwas Besonderes, etwas das Tiefe ausdrückt, oder man mehrmals hinsehen muss um etwas zu erkennen oder etwas das mehr Interpretationsspielraum lässt.
Gerne auch viel weiß, zumindest heller und nicht zu dunkel. Stylish, aber nicht überfrachtet.
Schreib mich gerne an, wenn du Fragen hast.
Ich habe mal zwei Beispiel von Typolösungen angehängt, die ich ganz cool fände.
Ich freue mich auf deine Ideen :-)
Ganz liebe Grüße
Mira

```html
<!DOCTYPE html>
<html lang="de">
<head>
<meta charset="utf-8">
<title>Morgenlicht NEU entdecken – Dr. Mira Kessow</title>
<link rel="stylesheet" href="https://fonts.googleapis.com/css2?family=Open+Sans:ital,wght@0,700;1,400&family=Poppins:wght@800&family=Sacramento&display=swap">
<style>
  :root {
    --bg-rose: #cd8fb4;
    --bg-violet: #6b4596;
    --bg-deep: #4a3274;
    --script-rose: #d99ac0;
    --text-white: #ffffff;
  }
  html, body {
    margin: 0;
    padding: 0;
    width: 858px;
    height: 1200px;
    overflow: hidden;
  }
  .cover {
    position: relative;
    width: 858px;
    height: 1200px;
    background:
      linear-gradient(152deg, var(--bg-rose) 0%, #a277aa 22%, var(--bg-violet) 52%, #573a88 72%, var(--bg-deep) 100%);
    color: var(--text-white);
    overflow: hidden;
  }
  .author {
    position: absolute;
    top: 36px;
    left: 0;
    width: 100%;
    margin: 0;
    text-align: center;
    font-family: "Open Sans", sans-serif;
    font-weight: 700;
    font-size: 44px;
    letter-spacing: 0.2px;
  }
  .title {
    margin: 0;
    font-weight: normal;
  }
  .title-script {
    position: absolute;
    font-family: "Sacramento", cursive;
    color: var(--script-rose);
    font-size: 104px;
    line-height: 1;
    white-space: nowrap;
  }
  .title-script--top {
    left: 100px;
    top: 388px;
  }
  .title-script--bottom {
    right: 96px;
    top: 578px;
  }
  .title-main {
    position: absolute;
    left: 0;
    top: 486px;
    width: 100%;
    text-align: center;
    font-family: "Poppins", sans-serif;
    font-weight: 800;
    font-size: 128px;
    line-height: 1;
    letter-spacing: 1px;
    color: var(--text-white);
  }
  .subtitle {
    position: absolute;
    right: 128px;
    top: 696px;
    margin: 0;
    text-align: right;
    font-family: "Open Sans", sans-serif;
    font-style: italic;
    font-weight: 400;
    font-size: 27px;
    line-height: 1.3;
  }
</style>
</head>
<body>
  <main class="cover">
    <p class="author">Dr. Mira Kessow</p>
    <h1 class="title">
      <span class="title-script title-script--top">Morgenlicht</span>
      <span class="title-main">NEU</span>
      <span class="title-script title-script--bottom">entdecken</span>
    </h1>
    <p class="subtitle">Spüre den Mut der ganz<br>in dir wohnt</p>
  </main>
</body>
</html>
```